Brivane Management

We need a web design for a new consulting company, with clients all over the world. The company provides management consulting to the travel industry.

Logo files are attached.

Website must look very corporate and be responsive in design.

Management Consulting

```html
<!DOCTYPE html>
<html lang="en">
<head>
<meta charset="utf-8">
<title>Brivane Strategy Management</title>
<link href="https://fonts.googleapis.com/css2?family=Lato:ital,wght@0,400;0,700;1,700&display=swap" rel="stylesheet">
<style>
:root{
  --bg-dark:#1e1e1e;
  --green:#62b22f;
  --green-dark:#4e9523;
  --blue:#1a73c0;
  --navy:#1d2e5c;
  --text:#333;
  --muted:#555;
  --panel:#fff;
  --band:#ebebeb;
  --grey-icon:#7a7a7a;
}
*{margin:0;padding:0;box-sizing:border-box}
html,body{width:1200px;height:1048px;overflow:hidden}
body{position:relative;background:radial-gradient(ellipse at center,#2c2c2c 0%,#161616 80%);font-family:'Lato',sans-serif;color:var(--text)}
.abs{position:absolute}
.side-visual{position:absolute;top:0;width:140px;height:1020px}
.side-visual.left{left:0;background:radial-gradient(ellipse at 0% 20%,#3a5a80 0%,rgba(40,40,40,0) 60%)}
.side-visual.right{right:0;background:radial-gradient(ellipse at 100% 80%,#3a5a80 0%,rgba(40,40,40,0) 60%)}
.topbar-phone{left:806px;top:14px;display:flex;align-items:center;gap:8px;color:#fff;font-size:21px;font-weight:700}
.topbar-phone .icon{width:30px;height:30px;border-radius:50%;background:var(--green);display:flex;align-items:center;justify-content:center}
.header-shape{left:0;top:0}
.brand{left:176px;top:64px;display:flex;align-items:center;gap:12px;height:46px}
.brand .mark{width:46px;height:46px;border-radius:50%;background:var(--blue);flex:none}
.brand .name{font-family:'Lato',sans-serif;font-size:17px;font-weight:700;color:var(--navy);white-space:nowrap}
.nav{left:544px;top:54px;height:67px;display:flex;align-items:center;font-size:19px;color:var(--text)}
.nav a{color:inherit;text-decoration:none;height:67px;display:flex;align-items:center}
.nav .active{background:var(--green);color:#fff;width:57px;justify-content:center;margin-right:35px}
.nav .item{margin-right:28px}
.hero{left:139px;top:121px;width:923px;height:397px;background:linear-gradient(100deg,#5d7896 0%,#8fa3bb 40%,#c8d3dd 70%,#dfe5ea 100%)}
.hero-copy{left:749px;top:216px;width:270px;font-size:19px;font-weight:700;font-style:italic;line-height:28px;color:#3c3c3c}
.cta{left:749px;top:334px;width:209px;height:34px;background:#fff;display:flex;align-items:center;font-size:16px;font-weight:700;font-style:italic;color:#111;box-shadow:0 1px 3px rgba(0,0,0,.3)}
.cta .chev{width:34px;height:34px;background:var(--green);display:flex;align-items:center;justify-content:center;margin-right:9px}
.slide-btn{width:40px;height:40px;border-radius:50%;background:#f2f2f2;border:2px solid #ccc;display:flex;align-items:center;justify-content:center;top:288px}
.content{left:139px;top:518px;width:923px;height:340px;background:var(--panel)}
.services-shape{left:0;top:0}
.service-label{top:551px;width:120px;text-align:center;font-size:15px;color:#222}
.welcome-title{left:156px;top:608px;font-size:18px;color:#222}
.welcome-title span{color:var(--blue)}
.rule{height:1px;border-top:1px dashed #999}
.dot{width:8px;height:8px;border-radius:50%;background:var(--navy)}
.welcome-text{left:160px;top:655px;width:604px;font-size:12.4px;line-height:16.8px;color:#333}
.welcome-text b{font-size:11px;color:#111}
.why{left:160px;top:718px;width:600px;height:118px;background:var(--green);box-shadow:0 4px 5px rgba(0,0,0,.25)}
.why-photo{left:14px;top:16px;width:130px;height:80px;background:linear-gradient(180deg,#bcc7d2,#6b7683);border:2px solid #fff}
.why h3{position:absolute;left:159px;top:14px;font-size:16px;font-weight:400;color:#fff}
.why p{position:absolute;left:159px;top:38px;width:428px;font-size:12.4px;line-height:16.5px;color:#fff}
.news-title{left:794px;top:600px;font-size:18.5px;color:var(--navy)}
.news-title span{color:var(--blue)}
.news-item{left:796px;width:246px;height:60px}
.date{position:absolute;left:0;top:0;width:32px;height:44px;text-align:center;color:#fff}
.date .d{background:var(--blue);height:25px;font-size:18px;font-weight:700;line-height:25px}
.date .m{background:#1f1f1f;height:19px;font-size:11px;font-weight:700;line-height:19px}
.news-item h4{position:absolute;left:45px;top:-3px;font-size:13.5px;font-weight:400;color:#222}
.news-item p{position:absolute;left:45px;top:14px;font-size:12.5px;color:#333}
.news-item a{position:absolute;left:45px;top:32px;font-size:11px;font-weight:700;color:var(--blue);text-decoration:none}
.news-sep{left:794px;width:248px;border-top:1px dashed #aaa}
.clients{left:139px;top:858px;width:923px;height:98px;background:var(--band)}
.clients-tab{left:554px;top:860px;width:118px;height:24px}
.clients-tab span{position:absolute;left:0;top:0;width:118px;text-align:center;font-size:18px;color:#fff;line-height:24px}
.client{top:902px;width:120px;text-align:center;font-size:22px;font-weight:700;color:#8d8d8d}
.footer-links{left:141px;top:977px;font-size:12.5px;font-weight:700;color:#fff}
.footer-links span{margin:0 10px;font-weight:400}
.footer-contact{font-size:12px;color:#fff;line-height:18px;white-space:nowrap}
.subscribe{left:800px;top:973px;display:flex;height:33px}
.subscribe .field{width:172px;background:#fff;border-radius:3px 0 0 3px;display:flex;align-items:center;padding-left:10px;gap:8px;font-size:11.5px;font-style:italic;color:#999}
.subscribe .btn{width:90px;background:var(--blue);color:#fff;font-size:13.5px;font-weight:700;display:flex;align-items:center;justify-content:center}
.bottom-bar{left:0;top:1021px;width:1200px;height:27px;background:var(--blue)}
.copyright{left:139px;top:1027px;font-size:12px;color:#fff}
.social{top:1024px;width:20px;height:20px;border-radius:50%;border:1.5px solid #fff}
</style>
</head>
<body>
<div class="side-visual left" role="img" aria-label="Glowing globe of screens at the left edge"></div>
<div class="side-visual right" role="img" aria-label="Glowing globe of screens at the right edge"></div>

<div class="abs topbar-phone">
  <span class="icon"><svg width="16" height="16" viewBox="0 0 24 24"><path fill="#fff" d="M6.6 10.8a15 15 0 0 0 6.6 6.6l2.2-2.2c.3-.3.7-.4 1-.2 1.1.4 2.3.6 3.6.6.6 0 1 .4 1 1V20c0 .6-.4 1-1 1A17 17 0 0 1 3 4c0-.6.4-1 1-1h3.5c.6 0 1 .4 1 1 0 1.3.2 2.5.6 3.6.1.3 0 .7-.2 1z"/></svg></span>
  123-456-7890
</div>

<div class="hero abs" role="img" aria-label="Businessman touching a virtual screen showing support services"></div>
<p class="abs hero-copy">Lorem ipsum dolor sit amet, consectetuer adipisemy nibh euismod tincidunt utre magmi aliquam erat volutpat</p>
<div class="abs cta"><span class="chev"><svg width="12" height="16" viewBox="0 0 12 16"><path d="M2 1l7 7-7 7" stroke="#fff" stroke-width="3" fill="none"/></svg></span>Get Started With Us !</div>
<div class="abs slide-btn" style="left:119px"><svg width="12" height="14" viewBox="0 0 12 14"><path d="M9 1L3 7l6 6" stroke="#333" stroke-width="3" fill="none"/></svg></div>
<div class="abs slide-btn" style="left:1037px"><svg width="12" height="14" viewBox="0 0 12 14"><path d="M3 1l6 6-6 6" stroke="#333" stroke-width="3" fill="none"/></svg></div>

<svg class="abs header-shape" width="1200" height="160" viewBox="0 0 1200 160">
  <polygon points="144,54 1062,54 1062,40 1116,88 1062,136 1062,121 144,121" fill="#fff"/>
</svg>
<div class="abs brand">
  <span class="mark"></span>
  <span class="name">Brivane Strategy Management, Inc.</span>
</div>
<nav class="abs nav">
  <a class="active" href="#">Home</a>
  <a class="item" href="#">About Us</a>
  <a class="item" href="#">Our Services</a>
  <a class="item" href="#">Contact Us</a>
</nav>

<div class="content abs"></div>
<svg class="abs services-shape" width="1200" height="600" viewBox="0 0 1200 600">
  <polygon points="246,518 288,518 288,580" fill="#555"/>
  <polygon points="960,518 918,518 918,580" fill="#555"/>
  <polygon points="282,434 918,434 944,518 918,584 282,584 256,518" fill="#fff"/>
  <g>
    <circle cx="379" cy="502" r="46" fill="var(--green)" stroke="#eee" stroke-width="4"/>
    <circle cx="491" cy="502" r="46" fill="var(--grey-icon)" stroke="#eee" stroke-width="4"/>
    <circle cx="601" cy="502" r="46" fill="var(--grey-icon)" stroke="#eee" stroke-width="4"/>
    <circle cx="714" cy="502" r="46" fill="var(--grey-icon)" stroke="#eee" stroke-width="4"/>
    <circle cx="826" cy="502" r="46" fill="var(--grey-icon)" stroke="#eee" stroke-width="4"/>
    <rect x="365" y="486" width="26" height="30" fill="none" stroke="#fff" stroke-width="3"/>
    <path d="M372 496h12M372 504h12" stroke="#fff" stroke-width="2.5"/>
    <path d="M476 487l30 30M506 487l-30 30" stroke="#fff" stroke-width="5" stroke-linecap="round"/>
    <path d="M588 518h28" stroke="#fff" stroke-width="2"/>
    <rect x="590" y="500" width="6" height="16" fill="#fff"/><rect x="599" y="490" width="6" height="26" fill="#fff"/><rect x="608" y="496" width="6" height="20" fill="#fff"/>
    <circle cx="714" cy="502" r="18" fill="none" stroke="#fff" stroke-width="3"/>
    <path d="M696 502h36M714 484v36" stroke="#fff" stroke-width="2"/>
    <circle cx="826" cy="502" r="18" fill="none" stroke="#fff" stroke-width="3"/>
    <circle cx="826" cy="502" r="10" fill="none" stroke="#fff" stroke-width="3"/>
    <circle cx="826" cy="502" r="3" fill="#fff"/>
  </g>
</svg>
<div class="abs service-label" style="left:319px">Planning</div>
<div class="abs service-label" style="left:431px">Development</div>
<div class="abs service-label" style="left:541px">Analysis</div>
<div class="abs service-label" style="left:654px">Marketing</div>
<div class="abs service-label" style="left:766px">Solutions</div>

<h2 class="abs welcome-title" style="font-weight:400">Welcome to <span>Brivane Strategy Management, Inc.</span></h2>
<div class="abs rule" style="left:156px;top:638px;width:598px"></div>
<div class="abs" style="left:156px;top:637px;width:109px;height:2px;background:var(--navy)"></div>
<div class="abs dot" style="left:262px;top:634px"></div>
<p class="abs welcome-text">Lorem ipsum dolor sit amet, consectetu adipiscing elit, sed diam nonummy nibh euismod tincidunt ut laoreet dolore magna aliquam erat volutpat.&nbsp; wisi enim ad minim veniam, quisLorem ipsum dolor sit amet, consectetu adipiscing elit, sed diam ...<b>Read more</b></p>

<div class="abs why">
  <div class="abs why-photo" role="img" aria-label="Business team shaking hands"></div>
  <h3>Why Choose Us</h3>
  <p>Lorem ipsum dolor sit amet, consectetu adipiscing elit, sed diam nonummy nibh euismod tincidunt ut laoreet dolore magna aliquam erat volutpat.&nbsp; wisi enim ad minim veniam.</p>
</div>

<h2 class="abs news-title" style="font-weight:400">News &amp; <span>Events</span></h2>
<svg class="abs" style="left:1028px;top:607px" width="16" height="14" viewBox="0 0 16 14"><path d="M6 2L1 7l5 5z" fill="var(--green)"/><path d="M10 2l5 5-5 5z" fill="var(--green)"/></svg>
<div class="abs rule" style="left:794px;top:629px;width:248px;border-top:1px solid #999"></div>
<div class="abs dot" style="left:900px;top:626px"></div>

<div class="abs news-item" style="top:656px"><div class="date"><div class="d">25</div><div class="m">OCT</div></div><h4>Start Velora Website</h4><p>Lorem ipsum dolor sit amet ellit.</p><a href="#">Read More...</a></div>
<div class="abs news-sep" style="top:708px"></div>
<div class="abs news-item" style="top:729px"><div class="date"><div class="d">25</div><div class="m">OCT</div></div><h4>Start Velora Website</h4><p>Lorem ipsum dolor sit amet ellit.</p><a href="#">Read More...</a></div>
<div class="abs news-sep" style="top:781px"></div>
<div class="abs news-item" style="top:802px"><div class="date"><div class="d">25</div><div class="m">OCT</div></div><h4>Start Velora Website</h4><p>Lorem ipsum dolor sit amet ellit.</p><a href="#">Read More...</a></div>

<div class="abs clients"></div>
<svg class="abs clients-tab" viewBox="0 0 118 24" width="118" height="24"><polygon points="8,0 118,0 110,24 0,24" fill="#5b5b5b"/></svg>
<div class="abs clients-tab"><span>Our Clients</span></div>
<div class="abs client" style="left:270px">Halvero</div>
<div class="abs client" style="left:401px">Quintal</div>
<div class="abs client" style="left:535px">Moravo</div>
<div class="abs client" style="left:674px">Tessel</div>
<div class="abs client" style="left:805px">Dravik</div>

<div class="abs footer-links">Home<span>|</span>About Us<span>|</span>Services<span>|</span>Contact Us</div>
<svg class="abs" style="left:437px;top:978px" width="10" height="14" viewBox="0 0 10 14"><path d="M5 0a5 5 0 0 1 5 5c0 4-5 9-5 9S0 9 0 5a5 5 0 0 1 5-5z" fill="#fff"/><circle cx="5" cy="5" r="2" fill="#222"/></svg>
<div class="abs footer-contact" style="left:456px;top:976px">Lorem ipsum dolor sit amet,<br>consectetuer adimpisciged</div>
<svg class="abs" style="left:616px;top:980px" width="12" height="12" viewBox="0 0 24 24"><path fill="#fff" d="M6.6 10.8a15 15 0 0 0 6.6 6.6l2.2-2.2c.3-.3.7-.4 1-.2 1.1.4 2.3.6 3.6.6.6 0 1 .4 1 1V20c0 .6-.4 1-1 1A17 17 0 0 1 3 4c0-.6.4-1 1-1h3.5c.6 0 1 .4 1 1 0 1.3.2 2.5.6 3.6.1.3 0 .7-.2 1z"/></svg>
<div class="abs footer-contact" style="left:634px;top:976px">123-456-7890</div>
<svg class="abs" style="left:616px;top:1003px" width="12" height="9" viewBox="0 0 12 9"><rect width="12" height="9" fill="#fff"/><path d="M0 0l6 5 6-5" stroke="#222" fill="none"/></svg>
<div class="abs footer-contact" style="left:634px;top:998px">info@brivanestrategy.com</div>

<div class="abs subscribe">
  <div class="field"><svg width="14" height="10" viewBox="0 0 14 10"><rect x=".5" y=".5" width="13" height="9" fill="none" stroke="#bbb"/><path d="M.5.5l6.5 5 6.5-5" stroke="#bbb" fill="none"/></svg>your e-mail address</div>
  <div class="btn">SUBSCRIBE</div>
</div>

<div class="abs bottom-bar"></div>
<div class="abs copyright">Copyright © 2014&nbsp; Brivane Strategy.All Right Reserved</div>
<div class="abs social" style="left:949px"></div>
<div class="abs social" style="left:976px"></div>
<div class="abs social" style="left:1004px"></div>
<div class="abs social" style="left:1032px"></div>
</body>
</html>
```